New Fun, Positive, energised looking Business Card Needed for High Achiever Coach

I am looking for a two sided full colour business card. I am self employed and have recently re branded my 1-2-1 work re-vitalising high achievers. My target client base for these cards is therefore high achievers - usually aged 40 -55, they are often entrepreneurs, CEO or work in banking and finance and 2/3 are male. I work with them on 90 day or 6 month coaching programs to help them live their success in a healthier, more sustainable and fulfiiled way. They pay for this privately so though they are corporate types the cards need not look 'corporate'. I want to portray the idea of transformation, vitality and re-connecting.
You can get a feel for the look I like on my new website: morvenlisk.co.uk
I want to use this logo with strapline (Re-Vitalising High Achievers) (I purchased off Logoharbor) and font/ colours (the turquoise and green).
Details to include on the card:
www.morvenlisk.co.uk
+44 7915 302618
morven@morvenlisk.co.uk
skype: morvenlisk
I'd also like to include:
Do you struggle to switch off? Want to be healthier and feel fitter? Want closer relationships? More clarity over the direction you are headed? I can help you do these things using integrated mind-body techniques. Visit morvenlisk.co.uk TODAY to apply for a FREE Breakthrough session.
BUT if that is too much text for a card I am open to advice/ammendments.
Updates
Thanks for your design - I am considering them. PLease change the wording to :

```html
<!DOCTYPE html>
<html lang="en">
<head>
<meta charset="utf-8">
<title>Morven Lisk – Business Card</title>
<link href="https://fonts.googleapis.com/css2?family=Open+Sans:wght@400;600;700&display=swap" rel="stylesheet">
<style>
  :root {
    --turquoise: #1ba3c9;
    --green: #5cb646;
    --silver-light: #f1f2f3;
    --silver-mid: #dcdfe1;
    --silver-dark: #c4c8cb;
    --ink: #444a4e;
    --backdrop: #eceae6;
    --white: #ffffff;
  }
  * { box-sizing: border-box; margin: 0; padding: 0; }
  html, body {
    width: 1200px; height: 720px; overflow: hidden;
    background: var(--backdrop);
    font-family: "Open Sans", Arial, sans-serif;
    color: var(--ink);
  }
  .canvas {
    width: 1200px; height: 720px;
    display: flex; align-items: center; justify-content: center; gap: 40px;
  }
  .card {
    position: relative;
    width: 540px; height: 310px;
    border-radius: 4px;
    overflow: hidden;
    background: linear-gradient(160deg, var(--silver-light) 0%, var(--silver-mid) 55%, var(--silver-dark) 100%);
    box-shadow: 0 6px 18px rgba(0,0,0,0.15);
  }

  /* Front */
  .card-front .wave { position: absolute; inset: 0; width: 100%; height: 100%; }
  .brand {
    position: absolute; left: 34px; top: 118px;
    display: flex; flex-direction: column; align-items: flex-start; gap: 4px;
  }
  .brand-row { display: flex; align-items: center; gap: 10px; }
  .brand-dot { width: 22px; height: 22px; border-radius: 50%; background: var(--green); }
  .brand-name { font-size: 28px; font-weight: 700; color: var(--turquoise); line-height: 1; }
  .brand-strapline { font-size: 11px; font-weight: 400; color: var(--turquoise); padding-left: 32px; }
  .contact-divider {
    position: absolute; left: 268px; top: 30px; width: 1px; height: 100px;
    background: var(--silver-dark);
  }
  .contact-list {
    position: absolute; left: 284px; top: 34px;
    list-style: none; display: flex; flex-direction: column; gap: 12px;
    font-size: 15px;
  }
  .contact-item { display: flex; align-items: center; gap: 8px; }
  .contact-icon { width: 16px; height: 16px; flex: none; }
  .website {
    position: absolute; right: 34px; bottom: 24px;
    font-size: 17px; font-weight: 600; letter-spacing: 2px; color: var(--white);
  }

  /* Back */
  .card-back {
    display: flex; flex-direction: column; align-items: center; justify-content: center;
    text-align: center; padding: 30px 36px;
  }
  .pitch { font-size: 17px; line-height: 1.35; }
  .pitch + .pitch { margin-top: 10px; }
  .pitch strong { font-weight: 700; }
</style>
</head>
<body>
<main class="canvas">

  <section class="card card-front" aria-label="Card front">
    <svg class="wave" viewBox="0 0 540 310" preserveAspectRatio="none" aria-hidden="true">
      <path d="M0 262 C 160 240, 300 200, 540 128 L540 310 L0 310 Z" fill="var(--turquoise)"/>
      <path d="M0 252 C 170 228, 320 180, 510 112" fill="none" stroke="var(--white)" stroke-width="8"/>
      <path d="M0 248 C 170 224, 320 176, 500 110" fill="none" stroke="var(--green)" stroke-width="3"/>
    </svg>

    <div class="brand">
      <div class="brand-row">
        <span class="brand-dot" aria-hidden="true"></span>
        <span class="brand-name">Morven Lisk</span>
      </div>
      <span class="brand-strapline">Re-Vitalising High Achievers</span>
    </div>

    <span class="contact-divider" aria-hidden="true"></span>
    <ul class="contact-list">
      <li class="contact-item">
        <svg class="contact-icon" viewBox="0 0 16 16" aria-hidden="true">
          <circle cx="8" cy="8" r="8" fill="var(--turquoise)"/>
          <path d="M5.2 4.2l1.4 1.6-.8 1.1c.5 1.2 1.4 2.1 2.6 2.6l1.1-.8 1.6 1.4-.9 1.4c-2.9-.3-5.4-2.8-5.7-5.7z" fill="var(--white)"/>
        </svg>
        <span>+44 7915 302618</span>
      </li>
      <li class="contact-item">
        <svg class="contact-icon" viewBox="0 0 16 16" aria-hidden="true">
          <circle cx="8" cy="8" r="8" fill="var(--turquoise)"/>
          <rect x="4" y="5.2" width="8" height="5.6" fill="var(--white)"/>
          <path d="M4 5.2l4 3 4-3" fill="none" stroke="var(--turquoise)" stroke-width="0.9"/>
        </svg>
        <span>morven@morvenlisk.co.uk</span>
      </li>
      <li class="contact-item">
        <svg class="contact-icon" viewBox="0 0 16 16" aria-hidden="true">
          <circle cx="8" cy="8" r="8" fill="var(--turquoise)"/>
        </svg>
        <span>morvenlisk</span>
      </li>
    </ul>

    <span class="website">www.morvenlisk.co.uk</span>
  </section>

  <section class="card card-back" aria-label="Card back">
    <p class="pitch">Do you struggle to switch off?<br>
      Want to be healthier and feel fitter?<br>
      Want closer relationships?<br>
      More clarity over the direction you are headed?</p>
    <p class="pitch">I can help you do these things using integrated<br>mind-body techniques.</p>
    <p class="pitch">Visit <strong>morvenlisk.co.uk</strong> TODAY to apply for a<br>FREE Breakthrough session.</p>
  </section>

</main>
</body>
</html>
```